Business card design for my company.
I would like the card's background colour to be black. You can also see our web site to get an idea of our brand. https://www.tmwhomecrafting.com.au/
- Name
- Email

```html
<!DOCTYPE html>
<html lang="en">
<head>
<meta charset="utf-8">
<title>TMW Home Crafting – Business Card</title>
<link rel="stylesheet" href="https://fonts.googleapis.com/css2?family=Roboto:wght@400;500&family=Exo+2:wght@700&display=swap">
<style>
  :root {
    --backdrop: #2b2b2c;
    --card: #1d1d1e;
    --card-edge: #0f9a3c;
    --brand-green: #14a84a;
    --text-light: #e9e9e9;
    --text-muted: #cfcfcf;
    --gloss-black: #0b0b0b;
  }
  * { box-sizing: border-box; margin: 0; padding: 0; }
  html, body {
    width: 1200px; height: 852px; overflow: hidden;
    background: var(--backdrop);
    font-family: "Roboto", Arial, sans-serif;
  }
  .stage { position: relative; width: 1200px; height: 852px; }

  .card {
    position: absolute;
    width: 520px; height: 300px;
    background: var(--card);
    border-radius: 18px;
    border-bottom: 7px solid var(--card-edge);
    box-shadow: 0 12px 28px rgba(0,0,0,.45);
    overflow: hidden;
  }
  .card--front { left: 90px; top: 110px; }
  .card--back  { left: 590px; top: 440px; }

  /* Front: brand side */
  .front-brand {
    position: absolute; left: 0; right: 0; top: 110px;
    display: flex; align-items: center; justify-content: center; gap: 12px;
  }
  .front-brand .brand-name {
    font-family: "Exo 2", "Roboto", sans-serif;
    font-weight: 700; font-size: 30px; letter-spacing: 1px;
    color: var(--gloss-black);
  }
  .front-brand .brand-mark {
    width: 14px; height: 14px; background: var(--gloss-black);
  }
  .front-web {
    position: absolute; left: 0; right: 0; bottom: 26px;
    text-align: center; color: var(--text-light);
    font-size: 14px;
  }

  /* Back: contact side */
  .back-brand {
    position: absolute; left: 34px; top: 196px;
    display: flex; align-items: center; gap: 9px;
  }
  .back-brand .brand-mark { width: 12px; height: 12px; background: var(--brand-green); }
  .back-brand .brand-name {
    font-family: "Exo 2", "Roboto", sans-serif;
    font-weight: 700; font-size: 20px; letter-spacing: .5px;
    color: var(--text-light);
  }
  .contact {
    position: absolute; left: 292px; top: 40px; right: 20px;
  }
  .contact .person-name {
    color: var(--brand-green); font-size: 20px; font-weight: 500;
  }
  .contact .person-role {
    color: var(--text-muted); font-size: 12.5px; margin-top: 2px;
  }
  .contact-list { list-style: none; margin-top: 24px; }
  .contact-list li {
    display: flex; align-items: center; gap: 10px;
    color: var(--text-light); font-size: 12.5px; line-height: 20px;
    white-space: nowrap;
  }
  .contact-list svg { width: 12px; height: 12px; fill: var(--brand-green); flex: none; }
</style>
</head>
<body>
<main class="stage">

  <section class="card card--front" aria-label="Card front">
    <div class="front-brand">
      <span class="brand-mark"></span>
      <span class="brand-name">TMW Home Crafting</span>
    </div>
    <p class="front-web">www.tmwhomecrafting.com.au</p>
  </section>

  <section class="card card--back" aria-label="Card back">
    <div class="back-brand">
      <span class="brand-mark"></span>
      <span class="brand-name">TMW Home Crafting</span>
    </div>

    <div class="contact">
      <p class="person-name">Liam Archer</p>
      <p class="person-role">General Manager</p>
      <ul class="contact-list">
        <li>
          <svg viewBox="0 0 24 24" aria-hidden="true"><path d="M6.6 10.8a15.1 15.1 0 0 0 6.6 6.6l2.2-2.2c.3-.3.7-.4 1-.2 1.1.4 2.3.6 3.6.6.6 0 1 .4 1 1V20c0 .6-.4 1-1 1A17 17 0 0 1 3 4c0-.6.4-1 1-1h3.5c.6 0 1 .4 1 1 0 1.3.2 2.5.6 3.6.1.3 0 .7-.2 1z"/></svg>
          0400 123 456
        </li>
        <li>
          <svg viewBox="0 0 24 24" aria-hidden="true"><path d="M2 5h20v14H2zm2 2v.5l8 5 8-5V7zm0 3v7h16v-7l-8 5z"/></svg>
          info@tmwhomecrafting.com.au
        </li>
        <li>
          <svg viewBox="0 0 24 24" aria-hidden="true"><path d="M12 2a10 10 0 1 0 0 20 10 10 0 0 0 0-20zm6.9 6h-3a15 15 0 0 0-1.3-3.9A8 8 0 0 1 18.9 8zM12 4c.9 1.2 1.6 2.5 2 4h-4c.4-1.5 1.1-2.8 2-4zM4.3 14a8 8 0 0 1 0-4h3.4a16 16 0 0 0 0 4zm.8 2h3a15 15 0 0 0 1.3 3.9A8 8 0 0 1 5.1 16zm3-8h-3a8 8 0 0 1 4.3-3.9C8.8 5.3 8.4 6.6 8.1 8zM12 20c-.9-1.2-1.6-2.5-2-4h4c-.4 1.5-1.1 2.8-2 4zm2.3-6H9.7a14 14 0 0 1 0-4h4.6a14 14 0 0 1 0 4zm.3 5.9c.6-1.2 1-2.5 1.3-3.9h3a8 8 0 0 1-4.3 3.9zm1.7-5.9a16 16 0 0 0 0-4h3.4a8 8 0 0 1 0 4z"/></svg>
          www.tmwhomecrafting.com.au
        </li>
        <li>
          <svg viewBox="0 0 24 24" aria-hidden="true"><path d="M12 2a7 7 0 0 0-7 7c0 5.3 7 13 7 13s7-7.7 7-13a7 7 0 0 0-7-7zm0 9.5A2.5 2.5 0 1 1 12 6.5a2.5 2.5 0 0 1 0 5z"/></svg>
          Kestrel Bay, Marlow Coast
        </li>
      </ul>
    </div>
  </section>

</main>
</body>
</html>
```